Need Business Card ASAP

We need a business card design for a meeting coming up in a few days. The company name is Harlow Ridge Building and Construction and the logo is attached. Something clean, cool, and contemporary that we can get to a printer right away. Attached is the business card for Volmar Energy, an affiliated company, which we like. Instead of the hawk on the back, you could use the attached "D". We'll also be needing matching letterhead in the near future, so ideas for that are welcome.

```html
<!DOCTYPE html>
<html lang="en">
<head>
<meta charset="utf-8">
<title>Harlow Ridge Building and Construction – Business Card</title>
<link rel="stylesheet" href="https://fonts.googleapis.com/css2?family=Source+Sans+3:wght@400;600;700&display=swap">
<style>
  :root {
    --backdrop: #e8e5de;
    --card-white: #ffffff;
    --band-grey: #dcdcdc;
    --rule-grey: #d3d3d3;
    --tan: #bfb584;
    --tan-light: #dcd9c3;
    --tan-mid: #c9c49f;
    --ink: #1d1d1d;
    --ink-soft: #333333;
    --icon-grey: #9b9b9b;
  }
  * { box-sizing: border-box; margin: 0; padding: 0; }
  html, body {
    width: 1034px; height: 1200px; overflow: hidden;
    background: var(--backdrop);
    font-family: "Source Sans 3", "Helvetica Neue", Arial, sans-serif;
  }
  .canvas { position: relative; width: 1034px; height: 1200px; }

  /* Front of card */
  .card-front {
    position: absolute; left: 64px; top: 56px; width: 888px; height: 506px;
    background: var(--card-white);
    box-shadow: 0 6px 18px rgba(0,0,0,.18);
  }
  .band { position: absolute; left: 0; width: 100%; background: var(--band-grey); }
  .band--top { top: 0; height: 73px; }
  .band--bottom { bottom: 0; height: 74px; }

  .company-header { position: absolute; top: 78px; left: 0; width: 100%; text-align: center; }
  .company-name { color: var(--tan); font-weight: 700; font-size: 30px; line-height: 40px; }
  .company-address { color: var(--ink); font-size: 22px; line-height: 30px; }

  .rule { position: absolute; top: 158px; height: 6px; }
  .rule--grey { left: 0; width: 608px; background: var(--rule-grey); }
  .rule--tan { left: 621px; width: 267px; background: var(--tan); }

  .brand-block {
    position: absolute; left: 108px; top: 192px; width: 172px; height: 217px;
    display: flex; flex-direction: column; align-items: center; justify-content: center; gap: 14px;
  }
  .brand-square { width: 70px; height: 70px; background: var(--tan); }
  .brand-name {
    color: var(--ink); font-weight: 600; font-size: 20px; line-height: 24px; text-align: center;
  }

  .divider {
    position: absolute; left: 308px; top: 192px; width: 3px; height: 212px;
    background: linear-gradient(to bottom, #ffffff, #b9b9b9 50%, #ffffff);
  }

  .contact { position: absolute; left: 335px; top: 182px; }
  .contact-name { color: var(--tan); font-weight: 700; font-size: 32px; line-height: 40px; }
  .contact-title { color: var(--ink-soft); font-weight: 700; font-size: 22px; line-height: 28px; margin-bottom: 14px; }
  .contact-list { list-style: none; }
  .contact-item {
    display: flex; align-items: center; gap: 8px;
    color: var(--ink); font-size: 23px; line-height: 39px;
  }
  .contact-icon { width: 17px; height: 17px; fill: var(--icon-grey); flex: none; }

  /* Back of card */
  .card-back {
    position: absolute; left: 59px; top: 600px; width: 888px; height: 511px;
    background: linear-gradient(to bottom, var(--tan-mid), var(--tan-light));
    box-shadow: 0 6px 18px rgba(0,0,0,.18);
    display: flex; align-items: center; justify-content: center; gap: 24px;
  }
  .back-square { width: 64px; height: 64px; background: var(--ink); }
  .back-name { color: var(--ink); font-weight: 700; font-size: 46px; line-height: 54px; }
</style>
</head>
<body>
<main class="canvas">
  <section class="card-front" aria-label="Business card front">
    <div class="band band--top"></div>
    <header class="company-header">
      <p class="company-name">Harlow Ridge Building and Construction</p>
      <p class="company-address">00, Complex Name, Street, City 00000</p>
    </header>
    <div class="rule rule--grey"></div>
    <div class="rule rule--tan"></div>

    <div class="brand-block">
      <div class="brand-square"></div>
      <p class="brand-name">Harlow Ridge<br>Building and<br>Construction</p>
    </div>
    <div class="divider"></div>

    <div class="contact">
      <p class="contact-name">Your Name</p>
      <p class="contact-title">Title</p>
      <ul class="contact-list">
        <li class="contact-item">
          <svg class="contact-icon" viewBox="0 0 16 16" aria-hidden="true"><path d="M3.5 1l3 3-1.6 1.8a9 9 0 0 0 5.3 5.3L12 9.5l3 3-2 2.5C6.5 14.5 1.5 9.5 1 3z"/></svg>
          (123) 456-7890
        </li>
        <li class="contact-item">
          <svg class="contact-icon" viewBox="0 0 16 16" aria-hidden="true"><path d="M5 0h6a1 1 0 0 1 1 1v14a1 1 0 0 1-1 1H5a1 1 0 0 1-1-1V1a1 1 0 0 1 1-1zm0 2v10h6V2zm3 11a1 1 0 1 0 0 2 1 1 0 0 0 0-2z"/></svg>
          (123) 456-7890
        </li>
        <li class="contact-item">
          <svg class="contact-icon" viewBox="0 0 16 16" aria-hidden="true"><path d="M1 3h14v10H1zM2 4l6 5 6-5v-.1H2z"/></svg>
          yourname@harlowridgebuild.com
        </li>
        <li class="contact-item">
          <svg class="contact-icon" viewBox="0 0 16 16" aria-hidden="true"><path d="M8 1a7 7 0 1 0 0 14A7 7 0 0 0 8 1zm0 1.3c.8.9 1.4 2.2 1.6 3.7H6.4C6.6 4.5 7.2 3.2 8 2.3zM2.4 7h2.9a11 11 0 0 0 0 2H2.4a5.7 5.7 0 0 1 0-2zm4 0h3.2a10 10 0 0 1 0 2H6.4a10 10 0 0 1 0-2zm4.3 0h2.9a5.7 5.7 0 0 1 0 2h-2.9a11 11 0 0 0 0-2zM6.4 10h3.2c-.2 1.5-.8 2.8-1.6 3.7-.8-.9-1.4-2.2-1.6-3.7z"/></svg>
          www.harlowridgebuild.com
        </li>
      </ul>
    </div>
    <div class="band band--bottom"></div>
  </section>

  <section class="card-back" aria-label="Business card back">
    <div class="back-square"></div>
    <p class="back-name">Harlow Ridge</p>
  </section>
</main>
</body>
</html>
```